Specialised investor in e-mobility and energy wants business card design

We need a business card design that fits our existing corporate design. <The look and feel must be 'sharp'/'clean', dynamic, communicate momentum, professionalism etc (as one would imagine from a firm in the financial sector). We like the idea of a reverse-side of the card that includes the logo, and the name and contact details on the other. We expect the deliverable to be whatever format might be required to be able to get cards printed directly by a service such as kelmo press. Our website is www.zub.capital

```html
<!DOCTYPE html>
<html lang="en">
<head>
<meta charset="utf-8">
<title>Zub Capital – Business Card</title>
<link href="https://fonts.googleapis.com/css2?family=Montserrat:wght@400;500;700&display=swap" rel="stylesheet">
<style>
  :root {
    --forest: #2f4d23;
    --leaf: #8cb04b;
    --ink: #2b2b2b;
    --paper: #ffffff;
    --backdrop: #8a7a66;
  }
  html, body {
    margin: 0;
    padding: 0;
    width: 900px;
    height: 1200px;
    overflow: hidden;
    background: var(--backdrop);
    font-family: "Montserrat", sans-serif;
  }
  .canvas { position: relative; width: 900px; height: 1200px; }
  .card {
    position: absolute;
    left: 80px;
    width: 742px;
    height: 440px;
    border-radius: 40px;
    overflow: hidden;
  }
  .card--front { top: 132px; background: var(--paper); }
  .card--back { top: 640px; background: var(--forest); }

  .brand {
    position: absolute;
    display: flex;
    align-items: center;
    white-space: nowrap;
    font-weight: 500;
  }
  .brand__dot { border-radius: 50%; flex: none; }
  .card--front .brand {
    left: 26px; top: 222px; transform: translateY(-50%);
    font-size: 44px; color: var(--forest); gap: 14px;
  }
  .card--front .brand__dot { width: 22px; height: 22px; background: var(--forest); }
  .card--back .brand {
    left: 50%; top: 218px; transform: translate(-50%, -50%);
    font-size: 74px; color: var(--paper); gap: 22px;
  }
  .card--back .brand__dot { width: 36px; height: 36px; background: var(--paper); }

  .divider {
    position: absolute; left: 406px; top: 140px;
    width: 2px; height: 188px; background: var(--leaf);
  }
  .details { position: absolute; left: 461px; top: 136px; color: var(--ink); }
  .details__name {
    margin: 0; font-size: 27px; font-weight: 700; color: var(--forest); line-height: 1.1;
  }
  .details__role { margin: 2px 0 0; font-size: 16px; }
  .contact { list-style: none; margin: 24px 0 0; padding: 0; font-size: 16px; }
  .contact li { display: flex; align-items: center; gap: 12px; height: 22px; }
  .contact svg { width: 14px; height: 14px; fill: var(--leaf); flex: none; }
  .address { margin: 14px 0 0; font-size: 16px; line-height: 21px; }
</style>
</head>
<body>
<main class="canvas">
  <section class="card card--front">
    <div class="brand"><span class="brand__dot"></span>Zub Capital</div>
    <div class="divider"></div>
    <div class="details">
      <h1 class="details__name">Martin Ashcombe</h1>
      <p class="details__role">Owner</p>
      <ul class="contact">
        <li>
          <svg viewBox="0 0 16 16"><path d="M2 5c0-2 2-3 6-3s6 1 6 3v1h-3V5H5v1H2zM4 7h8l2 6H2z"/></svg>
          +41 79 555 0148
        </li>
        <li>
          <svg viewBox="0 0 16 16"><path d="M1 3h14v10H1zM2 4l6 5 6-5z" fill-rule="evenodd"/></svg>
          martin@zub.capital
        </li>
        <li>
          <svg viewBox="0 0 16 16"><circle cx="8" cy="8" r="7"/></svg>
          www.zub.capital
        </li>
      </ul>
      <p class="address">48 Meridian Road, Suite 210<br>Larkfield, PA 19020</p>
    </div>
  </section>

  <section class="card card--back">
    <div class="brand"><span class="brand__dot"></span>Zub Capital</div>
  </section>
</main>
</body>
</html>
```